A Small Coastal town of New Zealand book!

we want a cool book cover for our book titled; Wharepuke Bay & Its Hidden Western Coves - Old Stories, Diving, Tramping and places to see...

attached are some screenshots of books we found that were similar to the topic i cover.

also attached are some screenshots of some ideas i have been playing with my self with myself on canva...

i quite like the first one how he managed to put 5 images there without making it look too busy...

Tourists

Tourism

Serif
Sans Serif

• Nice coastal image and good fonts and text placement
• not to busy...

```html
<!DOCTYPE html>
<html lang="en">
<head>
<meta charset="utf-8">
<title>Wharepuke Bay – Book Cover</title>
<link rel="stylesheet" href="https://fonts.googleapis.com/css2?family=Bodoni+Moda:ital,opsz,wght@1,6..96,400;1,6..96,600&family=Libre+Caslon+Text:ital,wght@0,400;1,400;1,700&display=swap">
<style>
  :root {
    --forest-deep: #2f5a1c;
    --forest-light: #7fa62c;
    --sand: #e9e4dc;
    --shallow: #5cc0b4;
    --lagoon: #1d8f8a;
    --deep-sea: #0f5e63;
    --ink-light: #ffffff;
    --rule: #d8d1c4;
  }
  html, body {
    margin: 0;
    padding: 0;
    width: 759px;
    height: 1200px;
    overflow: hidden;
    background: #ffffff;
  }
  .cover {
    position: relative;
    width: 759px;
    height: 1200px;
    overflow: hidden;
  }
  .cover-photo {
    position: absolute;
    inset: 0;
    width: 759px;
    height: 1200px;
  }
  .rule {
    position: absolute;
    left: 283px;
    width: 167px;
    height: 6px;
    background: var(--rule);
  }
  .rule--top { top: 63px; }
  .rule--bottom { top: 1133px; }
  .cover-text {
    position: absolute;
    left: 0;
    width: 759px;
    margin: 0;
    text-align: center;
    color: var(--ink-light);
  }
  .title {
    top: 68px;
    font-family: "Bodoni Moda", "Didot", serif;
    font-style: italic;
    font-weight: 400;
    font-size: 118px;
    line-height: 1;
    letter-spacing: 1px;
  }
  .subtitle {
    top: 228px;
    font-family: "Libre Caslon Text", serif;
    font-style: italic;
    font-size: 28px;
    line-height: 1.2;
  }
  .tagline {
    top: 372px;
    font-family: "Libre Caslon Text", serif;
    font-style: italic;
    font-weight: 700;
    font-size: 22px;
    line-height: 42px;
    letter-spacing: 8px;
  }
  .author-label {
    top: 936px;
    font-family: "Libre Caslon Text", serif;
    font-size: 17px;
    letter-spacing: 11px;
    line-height: 1;
  }
  .author-name {
    top: 968px;
    font-family: "Bodoni Moda", serif;
    font-style: italic;
    font-weight: 600;
    font-size: 70px;
    line-height: 58px;
  }
</style>
</head>
<body>
<main class="cover">
  <svg class="cover-photo" role="img" aria-label="Aerial photo of a forested headland meeting a white sand beach with scattered rocks and clear turquoise water" viewBox="0 0 759 1200" preserveAspectRatio="none">
    <defs>
      <linearGradient id="shoreline" x1="0.3" y1="0" x2="0.55" y2="1">
        <stop offset="0" stop-color="var(--forest-deep)"/>
        <stop offset="0.25" stop-color="var(--forest-light)"/>
        <stop offset="0.42" stop-color="var(--forest-deep)"/>
        <stop offset="0.52" stop-color="var(--sand)"/>
        <stop offset="0.6" stop-color="var(--shallow)"/>
        <stop offset="0.78" stop-color="var(--lagoon)"/>
        <stop offset="1" stop-color="var(--deep-sea)"/>
      </linearGradient>
    </defs>
    <rect width="759" height="1200" fill="url(#shoreline)"/>
  </svg>

  <div class="rule rule--top"></div>
  <h1 class="cover-text title">Wharepuke</h1>
  <p class="cover-text subtitle">Bay and its Hidden Western Coves</p>
  <p class="cover-text tagline">old stories diving tramping<br>and places to see</p>
  <p class="cover-text author-label">BEST SELLING AUTHOR</p>
  <p class="cover-text author-name">Rowan<br>Tealby</p>
  <div class="rule rule--bottom"></div>
</main>
</body>
</html>
```